Business IT Services Billboard to attract local small businesses

We are Brivoqua, a premier Managed Service Provider (MSP) specializing in comprehensive IT services and VOIP phone solutions exclusively for businesses. Our goal is to create a dynamic and visually engaging billboard advertisement that not only highlights our cutting-edge IT solutions but also emphasizes our state-of-the-art VOIP phone services. This billboard should communicate our commitment to providing innovative, reliable, and holistic technology solutions.
See the attached supporting documentation.
Target Market(s)
small business
Industry/Entity Type
Information Technology
Colors
Designer to choose colors to be used in the design.
Look and feel
Each slider illustrates characteristics of the customer's brand and the style your logo design should communicate.

```html
<!DOCTYPE html>
<html lang="en">
<head>
<meta charset="utf-8">
<title>Brivoqua Billboard</title>
<link rel="stylesheet" href="https://fonts.googleapis.com/css2?family=Michroma&family=Orbitron:wght@900&family=Poppins:wght@600;700;800&display=swap">
<style>
  :root {
    --page-bg: #a9a9a9;
    --navy-deep: #0a2252;
    --navy: #0d3a8c;
    --brand-blue: #2aa3ff;
    --band-blue: #1c78c8;
    --ink: #0f1d33;
    --link-blue: #1e6fc2;
    --white: #ffffff;
    --photo-warm: #e9ddcd;
    --photo-cool: #9fb7d3;
  }
  html, body {
    margin: 0;
    padding: 0;
    width: 1049px;
    height: 1200px;
    overflow: hidden;
    background: var(--page-bg);
  }
  .billboard {
    position: absolute;
    left: 24px;
    top: 412px;
    width: 1000px;
    height: 376px;
    box-shadow: 10px 10px 14px rgba(0,0,0,0.45);
  }
  .billboard svg { display: block; }
  .kicker { font-family: "Poppins", sans-serif; font-weight: 800; fill: var(--white); }
  .brand-headline { font-family: "Orbitron", sans-serif; font-weight: 900; fill: var(--brand-blue); }
  .service-line { font-family: "Michroma", sans-serif; fill: var(--white); stroke: var(--white); stroke-width: 0.8; }
  .band-text { font-family: "Poppins", sans-serif; font-weight: 700; fill: var(--white); }
  .brand-name { font-family: "Poppins", sans-serif; font-weight: 800; fill: var(--link-blue); }
  .cta-text { font-family: "Poppins", sans-serif; font-weight: 700; fill: var(--ink); }
  .url-text { font-family: "Poppins", sans-serif; font-weight: 800; fill: var(--ink); letter-spacing: 2px; }
  .url-domain { fill: var(--link-blue); }
</style>
</head>
<body>
<div class="billboard">
  <svg width="1000" height="376" viewBox="0 0 1000 376" xmlns="http://www.w3.org/2000/svg">
    <defs>
      <linearGradient id="headerGradient" x1="0" y1="0" x2="1" y2="1">
        <stop offset="0" stop-color="var(--navy)"/>
        <stop offset="1" stop-color="var(--navy-deep)"/>
      </linearGradient>
      <linearGradient id="photoGradient" x1="0" y1="0" x2="1" y2="0">
        <stop offset="0" stop-color="var(--white)"/>
        <stop offset="0.18" stop-color="var(--photo-warm)"/>
        <stop offset="0.7" stop-color="var(--photo-cool)"/>
        <stop offset="1" stop-color="#d8dde4"/>
      </linearGradient>
    </defs>

    <rect class="sheet" x="0" y="0" width="1000" height="376" fill="var(--white)"/>
    <rect class="header-panel" x="0" y="0" width="1000" height="214" fill="url(#headerGradient)"/>

    <g class="team-photo" role="img" aria-label="Photo of a small office team working together at desks with a computer, one colleague standing and handing over papers">
      <rect x="600" y="214" width="400" height="162" fill="url(#photoGradient)"/>
      <rect x="935" y="168" width="65" height="46" fill="var(--photo-cool)" opacity="0.85"/>
    </g>

    <text class="kicker" x="51" y="67" font-size="31" textLength="896" lengthAdjust="spacing">ELEVATE YOUR BUSINESS WITH</text>

    <text class="brand-headline" x="51" y="156" font-size="84" textLength="563" lengthAdjust="spacingAndGlyphs">BRIVOQUA</text>
    <text class="service-line" x="645" y="120" font-size="34" textLength="303" lengthAdjust="spacingAndGlyphs">IT AND VOIP</text>
    <text class="service-line" x="645" y="156" font-size="34" textLength="247" lengthAdjust="spacingAndGlyphs">SERVICES</text>

    <rect class="tagline-band" x="51" y="184" width="872" height="43" rx="18" fill="var(--band-blue)"/>
    <text class="band-text" x="72" y="215" font-size="23" textLength="810" lengthAdjust="spacingAndGlyphs">IT AND VOIP SOLUTIONS TAILORED FOR YOUR BUSINESS SUCCESS</text>

    <text class="brand-name" x="51" y="301" font-size="24">Brivoqua</text>

    <text class="cta-text" x="176" y="273" font-size="20" textLength="387" lengthAdjust="spacingAndGlyphs">TRANSFORM YOUR TECH TODAY AT</text>
    <rect class="url-pill" x="172" y="290" width="395" height="45" rx="22" fill="var(--white)" stroke="var(--brand-blue)" stroke-width="2"/>
    <text class="url-text" x="369.5" y="323" font-size="26" text-anchor="middle">www.<tspan class="url-domain">brivoqua</tspan>.com</text>
  </svg>
</div>
</body>
</html>
```